Website for IT consulting Company

I need a website upgrade, the existing site content is ok, I would also like to add a testimonial page, the site should be something that is easy for us to update content. You use the content from www.kelvanbrook.com as an example. I will also post update logo and artwork. I also need a contact form with some type of validation or captcha.

I added Coded to the Project

Please omit Address maps

Target Market(s)

small business, service oriented companies. We provide IT Consulting, support and mangement

Industry/Entity Type

Information Technology

Coding

Number of Pages Required

1 page

Font styles to use
Serif
Sans Serif

Requirements
Must have
• Contain logo attached, and content from existing web site www.kelvanbrook.com.
• Also need to update content easily, and be movable to different platforms.
• There is a catch phrase
• "Let us worry about your technology…” “ so you don’t have to!”
• Should be included.
Nice to have
• Testimonial page, Project page where we can post new and past projects and pictures
Should not have
• none

```html
<!DOCTYPE html>
<html lang="en">
<head>
<meta charset="utf-8">
<title>Kelvanbrook – IT Consulting</title>
<link rel="stylesheet" href="https://fonts.googleapis.com/css2?family=Montserrat:wght@400;600&family=Open+Sans:wght@400;600&family=Roboto:wght@400;500&display=swap">
<style>
:root{
  --blue:#24a3dd;
  --blue-dark:#1b8fc6;
  --ink:#333;
  --muted:#555;
  --card:#efefef;
  --white:#fff;
  --footer:#1f83c0;
}
*{box-sizing:border-box;margin:0;padding:0}
html,body{width:1200px;height:2579px;overflow:hidden}
body{font-family:"Open Sans",Arial,sans-serif;color:var(--ink);background:var(--white);position:relative}
h1,h2,h3{font-weight:400}
.abs{position:absolute}

/* header */
.site-header{position:absolute;left:0;top:0;width:1200px;height:125px;background:var(--white)}
.brand{position:absolute;left:77px;top:38px;display:flex;align-items:center;gap:12px}
.brand-square{width:40px;height:40px;background:var(--blue)}
.brand-name{font-family:"Montserrat",sans-serif;font-weight:600;font-size:34px;color:#7b7f84;letter-spacing:1px}
.header-phone{position:absolute;right:77px;top:14px;font-family:"Roboto",sans-serif;font-weight:500;font-size:21px;color:var(--blue-dark);display:flex;align-items:center;gap:10px}
.main-nav{position:absolute;right:77px;top:68px;display:flex;gap:30px;font-size:16px;color:#444}
.main-nav a{color:inherit;text-decoration:none;position:relative;padding-bottom:41px}
.main-nav a.active::after{content:"";position:absolute;left:-4px;right:-4px;bottom:0;height:2px;background:var(--blue)}

/* hero */
.hero{position:absolute;left:0;top:125px;width:1200px;height:572px;background:linear-gradient(100deg,#8a7560 0%,#d8d2c6 35%,#eceae6 55%,#b7b2ab 80%,#776a5e 100%)}
.hero-title{position:absolute;top:95px;width:100%;text-align:center;font-family:"Montserrat",sans-serif;font-weight:400;font-size:44px;color:var(--white);text-shadow:0 2px 4px rgba(0,0,0,.35)}
.hero-tagline{position:absolute;top:170px;width:100%;text-align:center;font-size:24px;color:#111}
.btn-contact{position:absolute;left:497px;top:233px;width:204px;height:52px;border-radius:26px;background:var(--blue);color:var(--white);font-weight:600;font-size:17px;display:flex;align-items:center;justify-content:center;box-shadow:0 3px 6px rgba(0,0,0,.3)}

/* services band */
.services{position:absolute;left:0;top:697px;width:1200px;height:283px;background:var(--blue);color:var(--white)}
.service{position:absolute;top:-49px;width:330px;text-align:center}
.icon-tile{width:104px;height:104px;background:var(--blue);border-radius:6px;margin:0 auto;display:flex;align-items:center;justify-content:center}
.service h3{font-family:"Roboto",sans-serif;font-size:23px;line-height:24px;margin-top:12px}
.service p{font-size:15px;line-height:25px;margin-top:10px}

/* welcome */
.welcome-title{position:absolute;left:80px;top:1025px;font-family:"Roboto",sans-serif;font-size:41px;color:#1e78b8}
.welcome-title span{color:var(--blue)}
.welcome-text{position:absolute;left:80px;top:1092px;width:625px;font-size:15px;line-height:25px;color:var(--muted)}
.btn-read{position:absolute;left:77px;top:1220px;width:172px;height:50px;background:var(--blue);color:var(--white);border-radius:5px;font-size:18px;display:flex;align-items:center;justify-content:center;gap:8px}
.video-frame{position:absolute;left:738px;top:1033px;width:385px;height:237px;border:4px solid #cfd0d2}
.video-frame .media{width:100%;height:100%;background:linear-gradient(180deg,#c9ced3 0%,#9aa0a6 55%,#5f6368 100%)}

/* IT support band */
.it-support{position:absolute;left:0;top:1322px;width:1200px;height:431px;background:linear-gradient(90deg,#9ea1a5,#7e8186 60%,#6f7277)}
.it-support h2{position:absolute;top:50px;width:100%;text-align:center;font-family:"Roboto",sans-serif;font-size:40px;color:var(--white)}
.support-item{position:absolute;top:143px;width:300px;text-align:center;color:var(--white);font-family:"Roboto",sans-serif;font-size:22px}
.support-item .icon-tile{margin-bottom:28px}
.btn-view{position:absolute;left:524px;top:330px;width:152px;height:48px;background:var(--white);border-radius:5px;color:#444;font-size:17px;display:flex;align-items:center;justify-content:center;gap:8px}

/* testimonials */
.testimonials-title{position:absolute;top:1800px;width:100%;text-align:center;font-family:"Roboto",sans-serif;font-size:40px;color:var(--blue)}
.testimonial-card{position:absolute;left:181px;top:1888px;width:850px;height:167px;background:var(--card);border-bottom:3px solid var(--blue);box-shadow:0 14px 14px -8px rgba(0,0,0,.25)}
.testimonial-card::before{content:"";position:absolute;left:400px;top:-26px;border:26px solid transparent;border-top:0;border-bottom-color:var(--card)}
.quote-mark{position:absolute;font-family:Georgia,serif;font-size:130px;color:#d8d8d8;line-height:1}
.testimonial-card p{position:absolute;left:50px;right:50px;top:40px;text-align:center;font-size:15px;line-height:26px;color:var(--muted)}
.client{position:absolute;top:112px;width:100%;text-align:center;font-size:15px;color:var(--blue)}
.client::before{content:"";display:inline-block;width:14px;height:2px;background:var(--blue);vertical-align:middle;margin-right:10px}
.dots{position:absolute;top:2077px;left:576px;display:flex;gap:10px}
.dots i{width:12px;height:12px;border-radius:50%;background:#ccc}
.dots i.on{background:var(--blue)}

/* contact details */
.contact-band{position:absolute;left:0;top:2144px;width:1200px;height:179px;background:var(--blue);color:var(--white)}
.contact-item{position:absolute;top:30px;width:280px;text-align:center;font-size:15px;line-height:23px}
.ring{width:60px;height:60px;border:2px solid var(--white);border-radius:50%;margin:0 auto 14px;display:flex;align-items:center;justify-content:center}

/* form */
.form-area{position:absolute;left:0;top:2323px;width:1200px;height:210px;background:linear-gradient(90deg,#6e6a66,#9c9894 50%,#7d7a77)}
.field{position:absolute;border:1px solid rgba(255,255,255,.8);border-radius:4px;background:rgba(255,255,255,.06);color:var(--white);font-size:14px;padding:10px 20px}
.btn-submit{position:absolute;left:460px;top:2458px;width:625px;height:41px;background:var(--blue);color:var(--white);font-family:"Roboto",sans-serif;font-size:22px;display:flex;align-items:center;justify-content:center}

/* footer */
.site-footer{position:absolute;left:0;top:2533px;width:1200px;height:46px;background:var(--footer);color:var(--white);font-size:15px}
.copyright{position:absolute;left:80px;top:13px}
.copyright b{font-weight:600}
.social{position:absolute;right:72px;top:3px;display:flex;gap:22px}
.social i{width:40px;height:40px;background:var(--white);opacity:.3;display:block}
.social i:first-child{background:#777;opacity:1}
</style>
</head>
<body>

<header class="site-header">
  <div class="brand"><span class="brand-square"></span><span class="brand-name">KELVANBROOK</span></div>
  <div class="header-phone">
    <svg width="20" height="20" viewBox="0 0 24 24"><path fill="#555" d="M6.6 10.8c1.4 2.8 3.8 5.1 6.6 6.6l2.2-2.2c.3-.3.7-.4 1-.2 1.1.4 2.3.6 3.6.6.6 0 1 .4 1 1V20c0 .6-.4 1-1 1C10.6 21 3 13.4 3 4c0-.6.4-1 1-1h3.5c.6 0 1 .4 1 1 0 1.3.2 2.5.6 3.6.1.3 0 .7-.2 1z"/></svg>
    (555) 014-2280
  </div>
  <nav class="main-nav">
    <a class="active">Home</a><a>About</a><a>Projects</a><a>Support</a><a>Clients</a><a>Careers</a><a>Testimonials</a><a>Contact</a>
  </nav>
</header>

<section class="hero" role="img" aria-label="Photo of hands typing on a laptop at a desk beside a coffee mug">
  <h1 class="hero-title">KELVANBROOK.COM</h1>
  <p class="hero-tagline">Let us worry about your technology... So you don’t have to !</p>
  <div class="btn-contact">CONTACT US NOW</div>
</section>

<section class="services">
  <div class="service" style="left:70px">
    <div class="icon-tile"><svg width="56" height="56" viewBox="0 0 56 56" fill="none" stroke="#fff" stroke-width="4"><circle cx="22" cy="32" r="10"/><circle cx="38" cy="18" r="7"/><circle cx="22" cy="32" r="3" fill="#fff"/></svg></div>
    <h3>Managed IT Solutions</h3>
    <p>Our staff will design, service, administer<br>and maintain your IT needs. We are<br>well versed on all major operating<br>system, and network<br>appliances.</p>
  </div>
  <div class="service" style="left:435px">
    <div class="icon-tile"><svg width="60" height="56" viewBox="0 0 60 56" fill="none" stroke="#fff" stroke-width="3"><rect x="10" y="10" width="40" height="28" rx="2"/><path d="M4 44h52"/><path d="M22 30l16-14M34 30l-12-12"/></svg></div>
    <h3>Remote Diagnostic and<br>Support</h3>
    <p>Do you need a quick solution to a technical<br>problem? With our live remote-assistance tool,<br>a member of our support team can view your<br>desktop and share control of your mouse and<br>keyboard to get you on your way to a solution.</p>
  </div>
  <div class="service" style="left:803px">
    <div class="icon-tile"><svg width="56" height="56" viewBox="0 0 56 56" fill="none" stroke="#fff" stroke-width="4"><rect x="8" y="20" width="22" height="30" rx="11"/><path d="M19 20v10M24 20c0-10 10-12 14-8l10-6"/></svg></div>
    <h3>IT Infrastructure Design and<br>Installation</h3>
    <p>Do you have more than one site? Do you<br>need remote access? We can design and<br>implement LANS/WANS and VPN’s.  Make<br>your important data available to you<br>wherever you are.</p>
  </div>
</section>

<h2 class="welcome-title">WELCOME TO <span>KELVANBROOK.COM</span></h2>
<p class="welcome-text">&nbsp;Outsourcing is subcontracting a process, such as product design or manufacturing, to a third-party company.[1] The decision to outsource is often made in the interest of lowering firm costs, redirecting or conserving energy directed at the competencies of a particular business, or to make more efficient use of land, labor, capital...</p>
<div class="btn-read">READ MORE <span>»</span></div>
<div class="video-frame">
  <div class="media" role="img" aria-label="Video still of a business meeting in a bright office"></div>
  <svg class="abs" style="left:160px;top:92px" width="56" height="56" viewBox="0 0 56 56"><circle cx="28" cy="28" r="26" fill="rgba(0,0,0,.45)" stroke="#fff" stroke-width="2"/><path d="M23 18v20l16-10z" fill="#fff"/></svg>
</div>

<section class="it-support" role="img" aria-label="Soft-focus photo of a smiling support team">
  <h2>IT SUPPORT SOLUTIONS</h2>
  <div class="support-item" style="left:88px">
    <div class="icon-tile"><svg width="56" height="56" viewBox="0 0 56 56" fill="none" stroke="#fff" stroke-width="4"><circle cx="22" cy="32" r="10"/><circle cx="38" cy="18" r="7"/><circle cx="22" cy="32" r="3" fill="#fff"/></svg></div>
    Network Administration
  </div>
  <div class="support-item" style="left:450px">
    <div class="icon-tile"><svg width="60" height="56" viewBox="0 0 60 56" fill="none" stroke="#fff" stroke-width="3"><rect x="10" y="10" width="40" height="28" rx="2"/><path d="M4 44h52"/><path d="M22 30l16-14M34 30l-12-12"/></svg></div>
    Desktop Support
  </div>
  <div class="support-item" style="left:812px">
    <div class="icon-tile"><svg width="56" height="56" viewBox="0 0 56 56" fill="none" stroke="#fff" stroke-width="3"><rect x="16" y="12" width="32" height="24"/><path d="M32 36v8M24 46h16M8 10v34M4 10v10h8V10"/></svg></div>
    Network Cabling
  </div>
  <div class="btn-view">VIEW ALL <span>»</span></div>
</section>

<h2 class="testimonials-title">TESTIMONIALS</h2>
<div class="testimonial-card">
  <span class="quote-mark" style="left:8px;top:-8px">“</span>
  <span class="quote-mark" style="right:30px;top:50px">”</span>
  <p>Lorem Ipsum is simply dummy text of the printing and typesetting industry. Lorem Ipsum has been the industry's standard dummy text ever since the 1500s.</p>
  <div class="client">Client Name</div>
</div>
<div class="dots"><i></i><i class="on"></i><i></i></div>

<section class="contact-band">
  <div class="contact-item" style="left:48px">
    <div class="ring"><svg width="22" height="28" viewBox="0 0 22 28"><path fill="none" stroke="#fff" stroke-width="2.5" d="M11 26S2 16 2 10a9 9 0 0 1 18 0c0 6-9 16-9 16z"/><circle cx="11" cy="10" r="3" fill="#fff"/></svg></div>
    123 Building name,<br>City, Country - Zipcode
  </div>
  <div class="contact-item" style="left:460px">
    <div class="ring"><svg width="26" height="26" viewBox="0 0 24 24"><path fill="#fff" d="M6.6 10.8c1.4 2.8 3.8 5.1 6.6 6.6l2.2-2.2c.3-.3.7-.4 1-.2 1.1.4 2.3.6 3.6.6.6 0 1 .4 1 1V20c0 .6-.4 1-1 1C10.6 21 3 13.4 3 4c0-.6.4-1 1-1h3.5c.6 0 1 .4 1 1 0 1.3.2 2.5.6 3.6.1.3 0 .7-.2 1z"/></svg></div>
    555.014.2280
  </div>
  <div class="contact-item" style="left:880px">
    <div class="ring"><svg width="28" height="22" viewBox="0 0 28 22" fill="none" stroke="#fff" stroke-width="2.5"><rect x="2" y="2" width="24" height="18" rx="3"/><path d="M2 4l12 9 12-9"/></svg></div>
    info@kelvanbrook<br>group.com
  </div>
</section>

<section class="form-area" role="img" aria-label="Faded photo of a desk with laptop, notebook and camera">
</section>
<div class="field" style="left:116px;top:2353px;width:335px;height:42px">First Name</div>
<div class="field" style="left:116px;top:2405px;width:335px;height:42px">Phone</div>
<div class="field" style="left:116px;top:2457px;width:335px;height:42px">Email</div>
<div class="field" style="left:460px;top:2353px;width:625px;height:93px">Message</div>
<div class="btn-submit">SUBMIT</div>

<footer class="site-footer">
  <div class="copyright">© <b>KELVANBROOK.COM</b>  - 2017. All Rights Reserved.</div>
  <div class="social"><i></i><i></i><i></i><i></i><i></i></div>
</footer>

</body>
</html>
```